A Techincal Author needs a site to promote his Programming Books

The StudyAlong series is a collection of books focusing on building the same app with different technologies. The purpose of this project is to design a web site home page that can be used to sell the books.

Expected Deliverables
• StudyAlong Logo as Illustrator file
• Master graphic design files for any relevant web assets
• HTML and CSS for home page, if applicable

Target Market(s)

The target market for our series is web programmers. They are people who have some experience, but want to learn a new tool. Programmers are analytical, logical people who like structure in the things they do.

Here are some things our customers like:

• Chirply / Postbox
• Crown of Ashes / Hollow Tide / Salt Hollow
• SmartPhones, Tablets, Stridelets, and other tech gadgets.

The design should try to speak to that market.

Requirements
Must have
• The primary tasks for this project are:
• 1) Create "Study Along" Logo.
• * All “NetPivot” properties use a similar logo approach, with the NetPivot ball icon on the left, a reflection below it. The company name is on the right, roughly the same size as the ball icon. A tag line underneath the company name, roughly the same size as the reflection.
• * Company Name: Study Along
• * Tagline: Knowledge to Boost Your Career
• * Logo color is up to the discretion of the designer, but should be compatible with the site design.
• * Sample Logos for other NetPivot properties in Illustrator format are available as attachments to this project.
• 2) Design the Study Along Home Page.
• The home page should follow this format:
• * Logo
• * Nav Bar
• • Buy (The Home Page)
• • About
• • Contact
• * Main Content
• • Home page content detailed in attachment
• * Footer
• • Copyright notice
• • Links to other stuff we do ( net-pivot.example | marlonpeake.example | BeyondTheGrid.example )
Nice to have
• It would be nice to have a book as part of the home page content.
Should not have
• Please do not use the same color scheme as BeyondTheGrid.example or Plumvane.example or QueryTheMaven.example

```html
<!DOCTYPE html>
<html lang="en">
<head>
<meta charset="utf-8">
<title>Study Along — Knowledge to Boost Your Career</title>
<link rel="stylesheet" href="https://fonts.googleapis.com/css2?family=Roboto:wght@300;400;500;700&display=swap">
<style>
  :root {
    --coral: #f2675f;
    --orange: #f7a21b;
    --ink: #2f2f2f;
    --text: #555555;
    --slate: #4a4a4a;
    --cell: #ececec;
    --cell-empty: #f6f6f6;
    --band: #f3f3f3;
    --footer: #0d0d0d;
    --white: #ffffff;
  }
  * { box-sizing: border-box; margin: 0; padding: 0; }
  html, body { width: 831px; height: 1200px; overflow: hidden; }
  body { font-family: "Roboto", Arial, sans-serif; color: var(--text); background: var(--white); }

  .site-header { height: 60px; display: flex; align-items: center; justify-content: space-between; padding: 0 32px; }
  .brand { display: flex; align-items: center; gap: 8px; }
  .brand-dot { width: 24px; height: 24px; border-radius: 50%; background: var(--coral); }
  .brand-name { font-size: 22px; font-weight: 500; color: var(--ink); line-height: 1; }
  .brand-tagline { font-size: 7px; color: var(--coral); margin-top: 2px; letter-spacing: .2px; }
  .main-nav { display: flex; gap: 22px; }
  .main-nav a { font-size: 9px; color: var(--ink); text-decoration: none; text-transform: uppercase; letter-spacing: .4px; }

  .hero { position: relative; height: 260px; }
  .hero-photo { position: absolute; inset: 0; background: linear-gradient(120deg, #e6e6e6 0%, #d6d6d6 45%, #c9c3c0 75%, #dcdcdc 100%); }
  .hero-title { position: relative; text-align: center; padding-top: 36px; font-size: 26px; line-height: 32px; font-weight: 500; color: var(--ink); text-transform: uppercase; letter-spacing: .5px; }
  .signup { position: absolute; top: 112px; left: 152px; width: 528px; height: 78px; background: var(--coral); text-align: center; padding-top: 11px; }
  .signup-title { font-size: 10px; color: var(--white); text-transform: uppercase; letter-spacing: .6px; }
  .signup-row { display: flex; justify-content: center; gap: 10px; margin-top: 13px; }
  .signup-field { width: 176px; height: 20px; border-radius: 10px; background: var(--white); font-size: 8px; color: #999; text-align: left; padding: 5px 10px; }
  .signup-submit { width: 64px; height: 20px; border-radius: 10px; background: var(--ink); color: var(--white); font-size: 8px; line-height: 20px; text-transform: uppercase; }
  .slider-dots { position: absolute; top: 222px; left: 0; right: 0; display: flex; justify-content: center; gap: 8px; }
  .slider-dots span { width: 7px; height: 7px; border-radius: 50%; background: var(--ink); }

  .welcome { height: 90px; text-align: center; padding-top: 18px; }
  .welcome h1 { font-size: 19px; font-weight: 700; color: var(--ink); text-transform: uppercase; }
  .welcome p { width: 540px; margin: 8px auto 0; font-size: 9.5px; line-height: 13px; }

  .book { width: 528px; margin: 0 auto; height: 212px; text-align: center; }
  .book h2 { font-size: 18px; font-weight: 400; color: var(--ink); line-height: 26px; }
  .sample-btn { display: inline-block; margin-top: 6px; height: 18px; line-height: 18px; padding: 0 12px; background: var(--ink); color: var(--white); font-size: 7.5px; }
  .price-table { width: 528px; margin-top: 10px; border-collapse: separate; border-spacing: 0 2px; }
  .price-table td { height: 29px; vertical-align: middle; }
  .plan { width: 208px; background: var(--slate); color: var(--white); font-size: 9px; font-weight: 500; text-align: left; padding-left: 18px; }
  .price { width: 140px; background: var(--cell); color: var(--ink); font-size: 18px; font-weight: 700; }
  .buy-direct { width: 90px; background: var(--coral); color: var(--white); font-size: 7px; }
  .buy-store { width: 90px; background: var(--orange); color: var(--white); font-size: 7px; line-height: 9px; }
  .buy-none { background: var(--cell-empty); }

  .partners { height: 75px; margin-top: 10px; background: var(--band); display: flex; align-items: center; justify-content: center; gap: 60px; }
  .partner { display: flex; align-items: center; gap: 8px; font-size: 15px; font-weight: 700; color: #35355e; }
  .partner-mark { width: 22px; height: 22px; border-radius: 50%; background: #35355e; }

  .site-footer { position: absolute; top: 1120px; left: 0; width: 831px; height: 80px; background: var(--footer); text-align: center; padding-top: 24px; }
  .footer-nav { display: flex; justify-content: center; gap: 20px; }
  .footer-nav a { color: var(--white); font-size: 8px; text-decoration: none; text-transform: uppercase; letter-spacing: .4px; }
  .copyright { margin-top: 10px; color: #aaaaaa; font-size: 7px; }
</style>
</head>
<body>
  <header class="site-header">
    <div class="brand">
      <div class="brand-dot"></div>
      <div>
        <div class="brand-name">Study Along</div>
        <div class="brand-tagline">Knowledge to Boost Your Career</div>
      </div>
    </div>
    <nav class="main-nav">
      <a href="#">Home</a><a href="#">About Us</a><a href="#">Pricing</a><a href="#">Contact</a>
    </nav>
  </header>

  <section class="hero">
    <div class="hero-photo" role="img" aria-label="Soft-focus photo of a person working at a laptop"></div>
    <h2 class="hero-title">Knowledge to<br>Boost Your Career</h2>
    <div class="signup">
      <div class="signup-title">Sign up for a free sample</div>
      <div class="signup-row">
        <div class="signup-field">Your Name</div>
        <div class="signup-field">Email Address</div>
        <div class="signup-submit">Submit</div>
      </div>
    </div>
    <div class="slider-dots"><span></span><span></span></div>
  </section>

  <section class="welcome">
    <h1>Welcome to Study Along</h1>
    <p>Study Along walks you through building one app again and again with a new tool each time, so you can compare frameworks, learn patterns fast and bring real skills back to your team and your next big project.</p>
  </section>

  <section class="book">
    <h2>AxleJS 1.5 &amp; Strapform</h2>
    <span class="sample-btn">View Sample</span>
    <table class="price-table">
      <tr><td class="plan">With Mock Services</td><td class="price">$5.99</td><td class="buy-direct">Buy From Us</td><td class="buy-store">Buy From<br>Rivermart</td></tr>
      <tr><td class="plan">With NodalJS Services</td><td class="price">$5.99</td><td class="buy-direct">Buy From Us</td><td class="buy-store">Buy From<br>Rivermart</td></tr>
      <tr><td class="plan">With ColdForge Services</td><td class="price">$5.99</td><td class="buy-direct">Buy From Us</td><td class="buy-store">Buy From<br>Rivermart</td></tr>
      <tr><td class="plan">Buy Them All</td><td class="price">$9.99</td><td class="buy-direct">Buy From Us</td><td class="buy-none"></td></tr>
    </table>
  </section>

  <section class="book">
    <h2>AxleJS 2 &amp; Strapform</h2>
    <span class="sample-btn">View Sample</span>
    <table class="price-table">
      <tr><td class="plan">With Mock Services</td><td class="price">$5.99</td><td class="buy-direct">Buy From Us</td><td class="buy-store">Buy From<br>Rivermart</td></tr>
      <tr><td class="plan">With NodalJS Services</td><td class="price">$5.99</td><td class="buy-direct">Buy From Us</td><td class="buy-store">Buy From<br>Rivermart</td></tr>
      <tr><td class="plan">With ColdForge Services</td><td class="price">$5.99</td><td class="buy-direct">Buy From Us</td><td class="buy-store">Buy From<br>Rivermart</td></tr>
      <tr><td class="plan">Buy Them All</td><td class="price">$9.99</td><td class="buy-direct">Buy From Us</td><td class="buy-none"></td></tr>
    </table>
  </section>

  <section class="book">
    <h2>ReflexJS</h2>
    <span class="sample-btn">View Sample</span>
    <table class="price-table">
      <tr><td class="plan">With Mock Services</td><td class="price">$5.99</td><td class="buy-direct">Buy From Us</td><td class="buy-store">Buy From<br>Rivermart</td></tr>
      <tr><td class="plan">With NodalJS Services</td><td class="price">$5.99</td><td class="buy-direct">Buy From Us</td><td class="buy-store">Buy From<br>Rivermart</td></tr>
      <tr><td class="plan">With ColdForge Services</td><td class="price">$5.99</td><td class="buy-direct">Buy From Us</td><td class="buy-store">Buy From<br>Rivermart</td></tr>
      <tr><td class="plan">Buy Them All</td><td class="price">$9.99</td><td class="buy-direct">Buy From Us</td><td class="buy-none"></td></tr>
    </table>
  </section>

  <section class="partners">
    <div class="partner"><span class="partner-mark"></span>Plumvane.example</div>
    <div class="partner"><span class="partner-mark"></span>BeyondTheGrid.example</div>
  </section>

  <footer class="site-footer">
    <nav class="footer-nav">
      <a href="#">Home</a><a href="#">About Us</a><a href="#">Pricing</a><a href="#">Contact</a>
    </nav>
    <div class="copyright">© 2016 Study Along. All rights reserved.</div>
  </footer>
</body>
</html>
```